Business Card Design (NEW FILES)

ATTENTION: New vector files are available. Please update your design to reflect/use the new (better resolution) logo images.

Seeking a unique and professional business card design for a commercial drone photography/videography business. The layout should feature
the logo (attached) and include the following information:
Owen Tarrick
614-502-7738
www.skylarkreelworks.example
NRD Certified Remote Pilot

Owen Tarrick

```html
<!DOCTYPE html>
<html lang="en">
<head>
<meta charset="utf-8">
<title>Skylark Reelworks – Business Cards</title>
<link rel="stylesheet" href="https://fonts.googleapis.com/css2?family=Montserrat:wght@400;500;700&display=swap">
<style>
  :root {
    --bg: #dcdddf;
    --card: #ffffff;
    --navy: #1f2352;
    --orange: #ee8a3d;
    --shadow: rgba(0, 0, 0, 0.16);
  }
  * { box-sizing: border-box; margin: 0; padding: 0; }
  html, body {
    width: 1200px; height: 876px; overflow: hidden;
    background: var(--bg);
    font-family: "Montserrat", Arial, sans-serif;
  }
  .canvas {
    position: relative; width: 1200px; height: 876px;
    display: flex; align-items: center; justify-content: center; gap: 60px;
  }
  .card {
    position: relative; width: 500px; height: 286px;
    background: var(--card);
    box-shadow: 0 6px 18px var(--shadow);
  }
  .brand {
    display: flex; align-items: center; gap: 9px;
    color: var(--navy); font-weight: 500; letter-spacing: 0.01em;
    white-space: nowrap;
  }
  .brand-dot {
    width: 13px; height: 13px; border-radius: 50%;
    background: var(--orange); flex: none;
  }
  .card-front .brand {
    position: absolute; left: 26px; top: 72px; font-size: 18px;
  }
  .divider {
    position: absolute; left: 248px; top: 70px;
    width: 2px; height: 150px; background: var(--navy);
  }
  .details {
    position: absolute; left: 264px; top: 68px; color: var(--navy);
  }
  .name { font-size: 19px; font-weight: 700; letter-spacing: 0.03em; line-height: 1.2; }
  .role { font-size: 12px; color: var(--orange); margin-top: 3px; line-height: 1.3; }
  .cert { font-size: 11px; color: var(--navy); margin-top: 2px; margin-bottom: 12px; line-height: 1.3; }
  .contact { list-style: none; font-size: 11.5px; line-height: 1.8; }
  .contact li { display: flex; align-items: center; gap: 7px; white-space: nowrap; }
  .contact svg { width: 11px; height: 11px; fill: var(--orange); flex: none; }
  .card-back { display: flex; align-items: center; justify-content: center; }
  .card-back .brand { font-size: 28px; }
  .card-back .brand-dot { width: 18px; height: 18px; }
</style>
</head>
<body>
<main class="canvas">
  <section class="card card-front" aria-label="Business card front">
    <div class="brand"><span class="brand-dot"></span>Skylark Reelworks</div>
    <div class="divider"></div>
    <div class="details">
      <p class="name">OWEN TARRICK</p>
      <p class="role">Owner</p>
      <p class="cert">NRD Certified Remote Pilot</p>
      <ul class="contact">
        <li>
          <svg viewBox="0 0 24 24"><path d="M6.6 10.8a15.1 15.1 0 0 0 6.6 6.6l2.2-2.2a1 1 0 0 1 1-.25 11.4 11.4 0 0 0 3.6.57 1 1 0 0 1 1 1V20a1 1 0 0 1-1 1A17 17 0 0 1 3 4a1 1 0 0 1 1-1h3.5a1 1 0 0 1 1 1c0 1.25.2 2.46.57 3.6a1 1 0 0 1-.25 1z"/></svg>
          614-502-7738
        </li>
        <li>
          <svg viewBox="0 0 24 24"><path d="M2 5h20v14H2z M2 5l10 8 10-8" fill="none" stroke="#ee8a3d" stroke-width="2.5"/></svg>
          ot@skylarkreelworks.example
        </li>
        <li>
          <svg viewBox="0 0 24 24"><circle cx="12" cy="12" r="10" fill="none" stroke="#ee8a3d" stroke-width="2.5"/><path d="M2 12h20M12 2c3 3 3 17 0 20M12 2c-3 3-3 17 0 20" fill="none" stroke="#ee8a3d" stroke-width="2"/></svg>
          www.skylarkreelworks.example
        </li>
      </ul>
    </div>
  </section>
  <section class="card card-back" aria-label="Business card back">
    <div class="brand"><span class="brand-dot"></span>Skylark Reelworks</div>
  </section>
</main>
</body>
</html>
```